Enlighted Feel-Good Wrapper Design for Cannabis Snack Bar: Vesko Bites.

We need a logo and wrapper for the first product in our line-up, Pip Crackle Maple! - Honey Salted Nuts and Dark Chocolate. Please highlight the name Maple Pip Crackle!, more than the name Vesko Bites or flavor of the bar. The package dimensions unfolded and unsealed are 6.5 inches x 5.25 inches. I have uploaded 3 photos of similar bar wrappers as an example of the wrapper type. The winning design will be awarded an extra amount for the Vesko Bites logo from Craft Hive.

It is a nut based snack bar similar to brands like Brisk, Stellar Munch, Orla, and Rover Bars. The difference is that this bar will contain THC and/or CBD oils. It is designed for the Medical Marijuana market in California. I would like the bar to be more upscale in design as we are going after a demographic with a higher disposable income and will be in their 30's-60's. We would like the brand to be appealing to both men and women. We would like the wrapper/logo to have an air of enlightenment to it. We want people to feel like they will be at peace when they eat this bar. Please do not make the design flashy, or decorated with marijuana leaves. We do not want something cheesy. We uploaded pictures of the bar so you can see what they look like. The packaging has to be OPAQUE.

Please include all the following. If you don't know specific values, weights or ingredients please fill the space with any text that can be substituted.

Label Regulatory Requirements:

(1) The identity of the product in a text size reasonably related to the most prominent printed matter on the panel;
(2) The words “cannabis-infused” immediately above the identity of the product in bold type and a text size larger than the text size used for the identity of the product;
(3) The cannabis product symbol uploaded in this post. The symbol shall be no smaller in size than half (.5) inch by half (.5) inch and shall be printed legibly and conspicuously;
(4) The net weight or volume of the contents of the package;

1.4 oz (40g)

(5) The THC content and CBD content for the package in its entirety, expressed in milligrams per package;

40mg

(6) The THC content and CBD content per serving, expressed in milligrams per serving;

10mg

(b) The primary panel text must be in type size no less than 6 point font and be in relation to the size of the primary panel and container.

40408. Informational Panel Labeling Requirements.
(a) The label for a medical cannabis product shall include an informational panel that includes the following:
(1) The licensed manufacturer and its contact number or website address;

Vesko Bites, San Diego, CA (555)302-7194, www.veskobites.example

(2) The date of manufacture;
(3) Each of the following statements:
(A) “SCHEDULE I CONTROLLED SUBSTANCE.”
(B) “KEEP OUT OF REACH OF CHILDREN AND ANIMALS” in bold print.
(C) “FOR MEDICAL USE ONLY.”
(D) “IF PREGNANT OR BREASTFEEDING, CONSULT A PHYSICIAN PRIOR TO USE.”
(E) “THE INTOXICATING EFFECTS OF THIS PRODUCT MAY BE DELAYED BY UP TO TWO HOURS.”
(F) “THIS PRODUCT MAY IMPAIR THE ABILITY TO DRIVE OR OPERATE MACHINERY, PLEASE USE EXTREME CAUTION.”
(4) A list of all product ingredients in descending order of predominance by weight or volume;

NUT MIXTURE:
almonds, peanuts, walnuts, puffed rice, flaxseed

SYRUP:
honey, brown rice syrup, sea salt, vanilla

CHOCOLATE DRIZZLE:
dark chocolate, coconut oil

(5) If an edible product that contains an ingredient, flavoring, coloring, or an incidental additive that bears or contains a major food allergen, the word “contains,” followed by a list of the applicable major food allergens;

Contains tree nuts.

(6) If an edible product, the names of any artificial food colorings contained in the product;
(7) If an edible product, the amount, in grams, of sodium, sugar, carbohydrates, and total fat per serving;

Dark Chocolate Sea Salt: 193 calories, 12.5g fat, 95mg sodium, 18.9g carbs, 2.1g fiber, 14g sugars, 5.2g protein

(8) The lot number;
(9) Instructions for use, such as the method of consumption or application, and any preparation necessary prior to use;
(10) The product expiration date, “use by” date, or “best by” date; and
(11) The unique identifier.
(b) The informational panel text shall be in a type size of no less than 6 point font and in relation to the size of the primary panel and container, unless there is insufficient area on the container available to print all the required information in a type size of no less than 6 point font. In such a case, the label shall include the warning statements required by paragraph (3) in a type size of no less than 6 point font, and the product shall be accompanied by a supplemental labeling that includes all of the information required by this section. The text of the supplemental labeling shall be no less than 8 point font.

The label shall not contain any of the following:

(a) Claims that the manufactured cannabis or cannabis product was grown in a California county when the cannabis was not grown there.
(b) The name of a California county unless the cannabis was grown there.
(c) Content that is or designed to be attractive to individuals under the age of 21, including but not limited to:
(1) Cartoons;
(2) Any likeness to images, characters, or phrases that are popularly used to advertise to children; or
(3) Any imitation of candy packaging or labeling.
(d) False labeling information. Labeling is false if it is false or misleading in any particular.
(e) Claims of health benefits or other physical benefits.
Updates

Industry/Entity Type

Retail

Logo Text

Vesko Bites

Colors

Designer to choose colors to be used in the design.

Requirements
Must have
• I would like to have a logo/icon of an cute owl or icon of a small tree branch with leaves and nut hanging off or anything else that you think would be a good logo incorporated with the company name "Vesko Bites." I uploaded a logo of an owl logo that I like. Feel free to adjust and create something creative, please do not copy it.
• The wrapper needs to reflect an upscale, natural, farm fresh, whole food product. We are trying to build a high end line of products that appeal to health conscious women and men ages 30 - 60 years old.
• Please include text from Allergen warning in one of the uploaded photos.
• Please add - "Gluten free" to the label, "Non GMO" or "GMO Free" and "No Soy" or "Soy Free", and "Dairy Free" as either writing or as an icon of some sort.
Nice to have
• Please see posted photos of some wrappers of food products that I like for ideas. Some color suggestions to incorporate: Red, Yellow, Green, Orange simply because these colors have been proven appealing to the eye for food labels. You may use one or a few of these and can balance them out with other colors. Please do not use traditional colors associated with cannabis such as dark brown or deep green. Subdued, natural looking versions of these may be okay if they are balanced out with other colors or the rest of the bar. I would also like the wrapper to have some graphics that can illustrate what the bar actually looks like so that people know whats inside!
• The final design should communicate:
• Freshness
• Organic
• Healthy
• Modern
Should not have
• I do not want this product to have graphics of typical cheesy cannabis/marijuana leaves or any other low class graphics related to the industry. Not graphics of marijuana flower, joints, smoke or leaves.

```html
<!DOCTYPE html>
<html lang="en">
<head>
<meta charset="utf-8">
<title>Vesko Bites – Maple Pip Crackle! wrapper concepts</title>
<link rel="stylesheet" href="https://fonts.googleapis.com/css2?family=Cinzel:wght@700&family=Montserrat:wght@800&family=Josefin+Sans:wght@400&family=Oswald:wght@600&family=Roboto+Condensed:wght@400&family=Libre+Baskerville:wght@700&display=swap">
<style>
  :root {
    --page: #ffffff;
    --wrap-white: #f4f4f4;
    --crimp-shade: #dedede;
    --red: #c8202a;
    --red-dark: #a5161f;
    --amber: #c98c2c;
    --gold: #f2bb2b;
    --cocoa: #3a1f1c;
    --cocoa-text: #3b2416;
    --sky: #5fb6dc;
    --bar-light: #d9b777;
    --bar-mid: #9a6a38;
    --bar-dark: #4a2a1a;
  }
  * { box-sizing: border-box; margin: 0; padding: 0; }
  html, body { width: 1200px; height: 1200px; overflow: hidden; background: var(--page); }
  .canvas { position: relative; width: 1200px; height: 1200px; background: var(--page); }

  .wrapper {
    position: absolute; width: 1010px; height: 368px;
    background: var(--wrap-white);
    overflow: hidden;
  }
  .wrapper--amber { left: 94px; top: 116px; }
  .wrapper--gold  { left: 98px; top: 584px; }

  .seal-left {
    position: absolute; left: 0; top: 0; width: 70px; height: 100%;
    background: repeating-linear-gradient(90deg, var(--red) 0 10px, var(--red-dark) 10px 12px);
  }
  .seal-right {
    position: absolute; right: 0; top: 0; width: 50px; height: 100%;
    background: repeating-linear-gradient(90deg, var(--wrap-white) 0 8px, var(--crimp-shade) 8px 10px);
  }

  .bar-photo {
    position: absolute; border-radius: 30px 40px 10px 10px;
    background: linear-gradient(100deg, var(--bar-light), var(--bar-mid) 30%, var(--bar-dark) 50%, var(--bar-light) 65%, var(--bar-mid) 85%, var(--bar-dark));
  }
  .wrapper--amber .bar-photo { left: 170px; top: 32px; width: 768px; height: 118px; }
  .wrapper--gold  .bar-photo { left: 165px; top: 32px; width: 775px; height: 118px; }

  .band-amber {
    position: absolute; left: 58px; top: 140px; width: 912px; height: 212px;
    background: var(--amber); border-radius: 6px 24px 6px 6px;
  }
  .band-gold {
    position: absolute; left: 310px; top: 144px; width: 636px; height: 190px;
    background: var(--gold); border-radius: 18px 40px 30px 60px;
  }

  .mascot {
    position: absolute; width: 96px; height: 132px;
    background: var(--gold); border-radius: 40px 40px 20px 20px;
  }
  .wrapper--amber .mascot { left: 194px; top: 36px; }
  .wrapper--gold  .mascot { left: 196px; top: 40px; }

  .infused-tag {
    position: absolute; width: 128px; height: 42px;
    background: var(--red);
    color: #fff; font-family: "Libre Baskerville", serif; font-weight: 700;
    font-size: 14px; line-height: 15px; text-align: center; padding-top: 6px;
  }
  .wrapper--amber .infused-tag { left: 82px; top: 118px; }
  .wrapper--gold  .infused-tag { left: 84px; top: 118px; }

  .brand-ribbon {
    position: absolute; left: 150px; top: 164px; width: 340px; height: 60px;
    background: var(--cocoa); border-radius: 6px;
    display: flex; align-items: center; justify-content: center;
  }
  .brand-ribbon::after {
    content: ""; position: absolute; left: 30px; right: 60px; bottom: -12px; height: 12px;
    background: var(--gold);
  }
  .brand-name {
    position: relative; z-index: 1;
    font-family: "Montserrat", sans-serif; font-weight: 800; font-size: 36px;
    color: #ffffff; letter-spacing: 1px; text-transform: uppercase; white-space: nowrap;
  }

  .thc-symbol { position: absolute; }
  .wrapper--amber .thc-symbol { left: 854px; top: 108px; width: 88px; height: 74px; }
  .wrapper--gold  .thc-symbol { left: 846px; top: 52px; width: 86px; height: 74px; }

  .net-weight {
    position: absolute; font-family: "Josefin Sans", sans-serif; font-size: 28px; color: var(--cocoa-text);
  }
  .wrapper--amber .net-weight { left: 94px; top: 306px; }
  .wrapper--gold  .net-weight { left: 92px; top: 262px; }

  .potency {
    position: absolute; font-family: "Roboto Condensed", sans-serif; font-size: 12.5px;
    line-height: 15px; color: var(--cocoa-text); white-space: nowrap;
  }
  .wrapper--amber .potency { left: 718px; top: 162px; }
  .wrapper--gold  .potency { left: 150px; top: 300px; }

  /* amber concept */
  .wrapper--amber .product-name {
    position: absolute; left: 300px; top: 244px;
    font-family: "Cinzel", serif; font-weight: 700; font-size: 37px; line-height: 44px;
    color: #fff; white-space: nowrap;
  }
  .wrapper--amber .flavor {
    position: absolute; left: 320px; top: 294px;
    font-family: "Libre Baskerville", serif; font-weight: 700; font-size: 18px; color: #fff;
    letter-spacing: 0.5px; white-space: nowrap;
  }
  .bar-drop {
    position: absolute; left: 832px; top: 214px; width: 86px; height: 32px;
    background: var(--gold); border-radius: 50%;
    font-family: "Cinzel", serif; font-weight: 700; font-size: 18px; color: #fff;
    text-align: center; line-height: 32px; letter-spacing: 2px;
  }
  .claims-stack {
    position: absolute; left: 818px; top: 262px; width: 124px;
    font-family: "Libre Baskerville", serif; font-weight: 700; font-size: 12.5px; line-height: 15px;
    color: var(--cocoa-text); text-align: center;
  }

  /* gold concept */
  .claims-line {
    position: absolute; left: 524px; top: 154px;
    font-family: "Josefin Sans", sans-serif; font-size: 14px; color: var(--red); white-space: nowrap;
  }
  .wrapper--gold .product-name {
    position: absolute; left: 330px; top: 236px;
    font-family: "Josefin Sans", sans-serif; font-weight: 400; font-size: 44px; line-height: 50px;
    color: var(--cocoa-text); white-space: nowrap;
  }
  .bar-word {
    position: absolute; left: 850px; top: 232px;
    font-family: "Josefin Sans", sans-serif; font-size: 24px; color: var(--cocoa-text);
  }
  .wrapper--gold .flavor {
    position: absolute; left: 388px; top: 288px;
    font-family: "Oswald", sans-serif; font-weight: 600; font-size: 24px; line-height: 32px;
    color: var(--cocoa-text); letter-spacing: 1.5px; white-space: nowrap;
  }
</style>
</head>
<body>
<main class="canvas">

  <section class="wrapper wrapper--amber" aria-label="Wrapper concept, amber band">
    <div class="seal-left"></div>
    <div class="seal-right"></div>
    <div class="bar-photo" role="img" aria-label="Photo of the nut bar with dark chocolate drizzle"></div>
    <div class="band-amber"></div>
    <div class="mascot" role="img" aria-label="Owl mascot illustration"></div>
    <div class="infused-tag">CANNABIS<br>INFUSED</div>
    <div class="brand-ribbon"><span class="brand-name">Vesko Bites</span></div>
    <p class="potency">THC content 40mg/pack<br>CBD content 10mg/serving</p>
    <svg class="thc-symbol" viewBox="0 0 88 74" aria-label="Cannabis product symbol">
      <polygon points="3,3 85,3 44,71" fill="var(--red)" stroke="var(--sky)" stroke-width="4" stroke-linejoin="round"/>
    </svg>
    <h1 class="product-name">MAPLE PIP CRACKLE!</h1>
    <div class="bar-drop">BAR</div>
    <p class="flavor">SALTED DARK CHOCOLATE &amp; NUTS</p>
    <p class="claims-stack">NON-GMO<br>GLUTEN-FREE<br>NO SOY<br>DAIRY-FREE</p>
    <p class="net-weight">40g</p>
  </section>

  <section class="wrapper wrapper--gold" aria-label="Wrapper concept, gold band">
    <div class="seal-left"></div>
    <div class="seal-right"></div>
    <div class="bar-photo" role="img" aria-label="Photo of the nut bar with dark chocolate drizzle"></div>
    <div class="band-gold"></div>
    <div class="mascot" role="img" aria-label="Owl mascot illustration"></div>
    <div class="infused-tag">CANNABIS<br>INFUSED</div>
    <div class="brand-ribbon"><span class="brand-name">Vesko Bites</span></div>
    <svg class="thc-symbol" viewBox="0 0 86 74" aria-label="Cannabis product symbol">
      <polygon points="3,3 83,3 43,71" fill="var(--red)" stroke="var(--sky)" stroke-width="4" stroke-linejoin="round"/>
    </svg>
    <p class="claims-line">• NON-GMO • GLUTEN-FREE • NO SOY • DAIRY-FREE</p>
    <h1 class="product-name">MAPLE PIP CRACKLE!</h1>
    <span class="bar-word">BAR</span>
    <p class="flavor">SALTED DARK CHOCOLATE &amp; NUTS</p>
    <p class="net-weight">40g</p>
    <p class="potency">THC content 40mg/pack<br>CBD content 10mg/serving</p>
  </section>

</main>
</body>
</html>
```